Business Card for a Dental Office

The design should communicate integrity, quality and reliability. We also want the card look elegant, simple, but still stand out, different from the traditional-dental-office business card.

Industry/Entity Type

Business

```html
<!DOCTYPE html>
<html lang="en">
<head>
<meta charset="utf-8">
<title>Harlow Dental Studio – Business Card</title>
<link rel="stylesheet" href="https://fonts.googleapis.com/css2?family=Oswald:wght@600&family=Open+Sans:wght@400;600&family=Open+Sans+Condensed:wght@700&display=swap">
<style>
  :root {
    --bg: #e9e6e2;
    --card-white: #ffffff;
    --ink: #111111;
    --black: #050505;
    --gold: #c9a81a;
    --gold-light: #e8cf2c;
    --gold-dark: #a88a14;
    --white: #ffffff;
  }
  * { margin: 0; padding: 0; box-sizing: border-box; }
  html, body { width: 1200px; height: 900px; overflow: hidden; background: var(--bg); }
  .canvas { position: relative; width: 1200px; height: 900px; }

  .card { position: absolute; overflow: hidden; box-shadow: 0 6px 18px rgba(0,0,0,.18); }

  /* Front */
  .card-front { left: 78px; top: 35px; width: 574px; height: 363px; background: var(--card-white); color: var(--ink); }
  .brand-name { position: absolute; left: 29px; top: 33px; font-family: "Oswald", sans-serif; font-weight: 600; font-size: 30px; letter-spacing: .3px; line-height: 1; color: var(--ink); white-space: nowrap; }
  .tagline { font-family: "Open Sans Condensed", "Open Sans", sans-serif; font-weight: 700; font-size: 14.5px; letter-spacing: .6px; text-transform: uppercase; color: var(--gold); line-height: 1; white-space: nowrap; }
  .card-front .tagline { position: absolute; left: 29px; top: 67px; }
  .person { position: absolute; left: 26px; top: 158px; font-family: "Open Sans", sans-serif; }
  .person-name { font-size: 22px; color: var(--gold); line-height: 1.2; }
  .person-role { font-size: 15px; margin-top: 2px; }
  .address { position: absolute; left: 25px; top: 222px; font-family: "Open Sans", sans-serif; font-size: 15px; line-height: 21px; }
  .contacts { position: absolute; left: 25px; top: 276px; list-style: none; font-family: "Open Sans", sans-serif; font-size: 15px; line-height: 21px; }
  .contacts li { display: flex; align-items: center; gap: 8px; }
  .contacts svg { width: 12px; height: 12px; fill: var(--gold); flex: none; }
  .accent-block { position: absolute; left: 435px; top: 125px; width: 139px; height: 238px; background: var(--black); border-left: 4px solid var(--gold-light); }

  /* Back */
  .card-back { left: 390px; top: 505px; width: 565px; height: 352px; background: var(--black); }
  .gold-block { position: absolute; left: 0; top: 117px; width: 138px; height: 235px; background: linear-gradient(135deg, var(--gold-light), var(--gold) 55%, var(--gold-dark)); border-right: 3px solid var(--white); }
  .signature { position: absolute; left: 216px; top: 268px; display: flex; align-items: center; gap: 10px; }
  .signature-square { width: 34px; height: 34px; background: var(--gold); flex: none; }
  .signature-name { font-family: "Oswald", sans-serif; font-weight: 600; font-size: 23px; line-height: 1; color: var(--white); letter-spacing: .2px; white-space: nowrap; }
  .card-back .tagline { font-size: 12.5px; margin-top: 3px; }
</style>
</head>
<body>
<main class="canvas">
  <section class="card card-front" aria-label="Business card front">
    <h1 class="brand-name">HARLOW DENTAL STUDIO</h1>
    <p class="tagline">A brighter smile starts right here</p>

    <div class="person">
      <p class="person-name">Marcus Ellery</p>
      <p class="person-role">Managing Director</p>
    </div>

    <p class="address">48 Linden Row<br>Ashford, 204518.</p>

    <ul class="contacts">
      <li><svg viewBox="0 0 24 24"><path d="M6.6 10.8a15 15 0 0 0 6.6 6.6l2.2-2.2a1 1 0 0 1 1-.25 11.4 11.4 0 0 0 3.6.57 1 1 0 0 1 1 1V20a1 1 0 0 1-1 1A17 17 0 0 1 3 4a1 1 0 0 1 1-1h3.5a1 1 0 0 1 1 1c0 1.25.2 2.450.57 3.57a1 1 0 0 1-.25 1z"/></svg>044-555 010 234</li>
      <li><svg viewBox="0 0 24 24"><path d="M2 5h20v14H2zm2 2v.5l8 5 8-5V7z"/></svg>hello@harlowdental.com</li>
      <li><svg viewBox="0 0 24 24"><path d="M10.6 13.4a1 1 0 0 1 0-1.4l3.5-3.5a1 1 0 1 1 1.4 1.4L12 13.4a1 1 0 0 1-1.4 0zM8 21a5 5 0 0 1-3.5-8.5l2-2 1.4 1.4-2 2a3 3 0 0 0 4.2 4.2l2-2 1.4 1.4-2 2A5 5 0 0 1 8 21zm9.5-7.5-1.4-1.4 2-2a3 3 0 0 0-4.2-4.2l-2 2-1.4-1.4 2-2a5 5 0 0 1 7 7z"/></svg>www.harlowdental.com</li>
    </ul>

    <div class="accent-block" aria-hidden="true"></div>
  </section>

  <section class="card card-back" aria-label="Business card back">
    <div class="gold-block" aria-hidden="true"></div>
    <div class="signature">
      <span class="signature-square" aria-hidden="true"></span>
      <div>
        <p class="signature-name">HARLOW DENTAL STUDIO</p>
        <p class="tagline">A brighter smile starts right here</p>
      </div>
    </div>
  </section>
</main>
</body>
</html>
```